Website for Apartment Rental in Prague

I would like to create designs of my website focused on luxury apartment rentals in Prague, Czech Republic. I created initial mock-ups, They are all attached. I need to design homepage and subpage. The mock-ups were created by combining elements from different websites that I liked but I need you to create a design that is unique and original. The attached files a only a guidance for the structure of the website but not for the design. Try to be creative.

Apartment

```html
<!DOCTYPE html>
<html lang="en">
<head>
<meta charset="utf-8">
<title>Vltava Suites – Prague Apartment Rentals</title>
<link rel="stylesheet" href="https://fonts.googleapis.com/css2?family=Nunito:wght@400;700;800&family=Open+Sans:wght@400;600;700&family=Tinos:wght@400;700&display=swap">
<style>
:root{
  --gold:#cf9f3b;
  --gold-light:#e0b458;
  --gold-deep:#b8862a;
  --ink:#1d1d1d;
  --ink-soft:#2b2b2b;
  --text:#555;
  --muted:#8a8a8a;
  --line:#d9d9d9;
  --white:#fff;
}
*{box-sizing:border-box;margin:0;padding:0}
html,body{width:1200px;height:4110px;overflow:hidden}
body{font-family:"Open Sans",Arial,sans-serif;color:var(--text);background:var(--white);position:relative}
.abs{position:absolute}
.photo{position:absolute;display:block}

/* top strip */
.topbar{position:absolute;left:0;top:0;width:1200px;height:38px}
.topbar__dark{position:absolute;left:590px;top:0;width:610px;height:38px;background:var(--ink);clip-path:polygon(22px 0,100% 0,100% 100%,0 100%)}
.topbar__links{position:absolute;right:80px;top:0;height:38px;display:flex;gap:46px;align-items:center;font-size:13px;color:#eee;letter-spacing:.5px}
.topbar__links span{display:flex;align-items:center;gap:8px}

/* header */
.header{position:absolute;left:0;top:38px;width:1200px;height:77px}
.brand{position:absolute;left:80px;top:18px;display:flex;align-items:center;gap:12px;font-family:"Nunito",sans-serif;font-weight:800;font-size:30px;color:var(--gold);letter-spacing:1px}
.brand__dot{width:16px;height:16px;border-radius:50%;background:var(--gold)}
.callus{position:absolute;right:85px;top:24px;display:flex;align-items:center;gap:16px;font-size:20px}
.callus__label{color:var(--gold)}
.callus__num{color:var(--ink-soft)}

/* nav */
.nav{position:absolute;left:0;top:115px;width:1200px;height:63px;background:var(--gold);display:flex;padding-left:80px}
.nav a{display:flex;align-items:center;padding:0 21px;color:var(--white);font-size:15px;text-decoration:none}
.nav a.is-active{background:var(--ink)}

/* hero */
.hero{position:absolute;left:0;top:178px;width:1200px;height:570px;overflow:hidden}
.hero__bg{left:0;top:0;width:1200px;height:570px;background:linear-gradient(90deg,#2a2623 0%,#4a4139 35%,#8f8478 60%,#d8d2ca 100%)}
.hero__kicker{left:148px;top:136px;color:var(--white);font-family:"Nunito",sans-serif;font-weight:800;font-size:27px;letter-spacing:.5px}
.hero__title{left:124px;top:168px;color:var(--white);font-family:"Nunito",sans-serif;font-weight:800;font-size:60px;letter-spacing:2px}
.hero__text{left:88px;top:250px;width:370px;color:#f0f0f0;font-size:14.5px;line-height:21px}
.btn{display:flex;align-items:center;justify-content:center;background:var(--gold);color:var(--white);font-family:"Nunito",sans-serif;font-weight:700;letter-spacing:.5px}
.hero__btn{position:absolute;left:159px;top:348px;width:211px;height:69px;font-size:20px}
.hero__thumb{border-radius:50%;border:5px solid var(--gold);background:#7c7267}
.hero__dots{left:575px;top:505px;display:flex;gap:8px}
.hero__dots i{width:14px;height:14px;background:#bbb;display:block}
.hero__dots i.on{background:var(--gold)}

/* booking */
.intro__title{left:0;top:808px;width:1200px;text-align:center;font-family:"Nunito",sans-serif;font-weight:800;font-size:35px;color:var(--ink)}
.accent{color:var(--gold)}
.intro__sub{left:190px;top:870px;width:820px;text-align:center;font-size:16px;line-height:26px;color:var(--text)}
.field__label{top:948px;font-size:15px;color:var(--gold)}
.field{top:986px;height:55px;border:1px solid var(--line);display:flex;align-items:center;justify-content:space-between;padding:0 14px;font-size:15px;color:#666}
.search{position:absolute;left:918px;top:986px;width:156px;height:55px;font-size:18px}

.promo{top:1088px;width:345px;height:304px}
.promo__img{left:0;top:0;width:345px;height:222px}
.promo__cap{position:absolute;left:0;top:222px;width:345px;height:82px;display:flex;flex-direction:column;align-items:center;justify-content:center;font-family:"Tinos",serif;font-size:16.5px;line-height:21px;color:var(--white);text-align:center}
.promo__cap--gold{background:var(--gold)}
.promo__cap--dark{background:var(--ink-soft)}

/* services */
.services{position:absolute;left:0;top:1471px;width:1200px;height:688px}
.services__bg{left:0;top:0;width:1200px;height:688px;background:linear-gradient(180deg,#1c1a18,#2d2925 60%,#231f1c)}
.services__title{left:0;top:60px;width:1200px;text-align:center;font-family:"Nunito",sans-serif;font-weight:800;font-size:35px;color:var(--white)}
.services__text{left:170px;top:124px;width:860px;text-align:center;color:#ddd;font-size:13.5px;line-height:26px}
.svc{top:272px;width:247px;height:334px}
.svc__box{position:absolute;left:0;top:98px;width:247px;height:192px;background:var(--white)}
.svc__img{left:24px;top:0;width:200px;height:200px;border-radius:50%;border:6px solid var(--white);background:#a59a8c}
.svc__badge{position:absolute;width:38px;height:38px;border-radius:50%;background:var(--gold);border:3px solid var(--white);color:var(--white);font-size:12px;font-weight:700;display:flex;align-items:center;justify-content:center}
.svc__cap{position:absolute;left:10px;top:224px;width:227px;text-align:center;color:var(--gold);font-size:14px;line-height:19px}
.svc__btn{position:absolute;left:0;top:290px;width:247px;height:44px;font-size:18px}

/* offers */
.thumb{left:77px;width:126px;background:#c8c3bb}
.offer__main{left:214px;top:2233px;width:520px;height:334px;background:linear-gradient(135deg,#e6e2dc,#c3bcb2)}
.offer__bar{position:absolute;left:214px;top:2512px;width:520px;height:55px;background:var(--gold);display:flex;justify-content:space-between;align-items:center;padding:0 32px;color:var(--white);font-size:17px}
.offer__title{left:773px;top:2240px;font-family:"Nunito",sans-serif;font-weight:800;font-size:35px;line-height:40px;color:var(--ink)}
.offer__text{left:767px;top:2326px;width:355px;font-size:14px;line-height:25px;color:var(--text)}
.offer__btn{position:absolute;left:767px;top:2496px;width:206px;height:69px;font-size:19px}

/* testimonial */
.voices{position:absolute;left:0;top:2650px;width:1200px;height:441px}
.voices__bg{left:0;top:0;width:1200px;height:441px;background:linear-gradient(180deg,#c89a3a,#d8ab4f 50%,#c79633)}
.voices__title{left:0;top:58px;width:1200px;text-align:center;font-family:"Nunito",sans-serif;font-weight:800;font-size:33px;color:var(--ink)}
.voices__avatar{left:547px;top:124px;width:106px;height:106px;border-radius:50%;border:4px solid var(--white);background:#e3d2b8}
.voices__quote{left:200px;top:245px;width:800px;text-align:center;color:var(--white);font-size:14px;line-height:24px}
.voices__name{left:0;top:306px;width:1200px;text-align:center;font-family:"Nunito",sans-serif;font-weight:700;font-size:20px;letter-spacing:1px;color:var(--ink)}
.voices__role{left:0;top:340px;width:1200px;text-align:center;font-size:13px;color:var(--ink-soft)}
.voices__dots{left:560px;top:382px;display:flex;gap:14px}
.voices__dots i{width:16px;height:16px;border-radius:50%;border:2px solid var(--white);display:block}
.voices__dots i.on{background:var(--white)}

/* blog */
.blog__title{left:0;top:3146px;width:1200px;text-align:center;font-family:"Nunito",sans-serif;font-weight:800;font-size:35px;color:var(--ink)}
.post{top:3225px;width:334px;height:380px}
.post__img{left:0;top:0;width:334px;height:186px}
.post__date{position:absolute;left:6px;top:176px;width:62px;height:88px;background:var(--white);border:4px solid var(--gold);display:flex;flex-direction:column;align-items:center;overflow:hidden}
.post__date b{width:100%;background:var(--gold);color:var(--white);font-family:"Nunito",sans-serif;font-size:25px;text-align:center;line-height:44px}
.post__date span{color:var(--gold);font-size:15px;line-height:36px}
.post__title{position:absolute;left:86px;top:198px;width:248px;font-family:"Nunito",sans-serif;font-weight:800;font-size:17px;line-height:21px;color:var(--gold)}
.post__text{position:absolute;left:0;top:278px;width:334px;font-size:14px;line-height:23px;color:var(--text)}

/* footer */
.footer{position:absolute;left:0;top:3685px;width:1200px;height:356px;background:linear-gradient(180deg,#1e1c1a,#2a2724)}
.footer h4{position:absolute;top:60px;font-family:"Nunito",sans-serif;font-weight:700;font-size:18px;color:var(--gold)}
.footer__about{position:absolute;left:77px;top:112px;width:250px;color:#ddd;font-size:14px;line-height:24px}
.footer__map{position:absolute;left:384px;top:110px;list-style:none;color:#ddd;font-size:13.5px;line-height:25px}
.footer__map li::before{content:"";display:inline-block;width:6px;height:6px;border-radius:50%;background:var(--gold);margin-right:12px;vertical-align:middle}
.footer__contact{position:absolute;left:586px;top:112px;color:#ddd;font-size:13.5px}
.footer__row{display:flex;gap:16px;align-items:flex-start;margin-bottom:24px;line-height:20px}
.footer__row svg{flex:none;margin-top:2px}
.footer__row b{color:var(--gold);font-weight:600}
.footer__news{position:absolute;left:877px;top:112px;width:246px;color:#eee;font-size:13.5px;line-height:22px}
.footer__input{margin-top:14px;width:244px;height:44px;background:var(--white);color:#777;font-size:13px;padding:0 12px;display:flex;align-items:center}
.footer__btn{margin-top:12px;width:160px;height:44px;font-size:17px}
.copy{position:absolute;left:0;top:4041px;width:1200px;height:69px;background:var(--gold);display:flex;align-items:center;justify-content:center;color:var(--white);font-size:13px}
</style>
</head>
<body>

<div class="topbar">
  <div class="topbar__dark"></div>
  <div class="topbar__links">
    <span>OUR HOSPITALITY</span>
    <span>DISCOVER PRAGUE <svg width="14" height="14" viewBox="0 0 14 14"><path d="M3 13V1h8l-2 3 2 3H4" fill="#cf9f3b"/></svg></span>
    <span>EN <svg width="10" height="6" viewBox="0 0 10 6"><path d="M0 0h10L5 6z" fill="#eee"/></svg></span>
  </div>
</div>

<header class="header">
  <div class="brand"><span class="brand__dot"></span>VLTAVA SUITES</div>
  <div class="callus">
    <span class="callus__label">Call Us Now</span>
    <svg width="24" height="24" viewBox="0 0 24 24"><path d="M6 2l4 4-2 3c1 3 4 6 7 7l3-2 4 4-3 4C10 21 3 14 2 5z" fill="#cf9f3b"/></svg>
    <span class="callus__num">+420 555 010 200</span>
  </div>
</header>

<nav class="nav">
  <a class="is-active">Home</a><a>Apartments</a><a>Location</a><a>Services</a><a>Gallery</a><a>News</a><a>Exclusive Offers &amp; Tours</a><a>For Families</a><a>Contact Us</a>
</nav>

<section class="hero">
  <div class="photo hero__bg" role="img" aria-label="Modern Prague apartment kitchen and living interior"></div>
  <div class="abs hero__kicker">BEING HOME IN</div>
  <div class="abs hero__title">PRAGUE</div>
  <p class="abs hero__text">Lorem Ipsum is simply dummy text of the printing and typesetting industry. Lorem Ipsum has been the industry's standard dummy text ever since the 1500s</p>
  <div class="hero__btn btn">LEARN MORE</div>
  <div class="photo hero__thumb" style="left:408px;top:70px;width:124px;height:124px" role="img" aria-label="Apartment interior detail"></div>
  <div class="photo hero__thumb" style="left:460px;top:228px;width:96px;height:96px" role="img" aria-label="Apartment bedroom detail"></div>
  <div class="photo hero__thumb" style="left:490px;top:388px;width:84px;height:84px" role="img" aria-label="Apartment living room detail"></div>
  <div class="abs hero__dots"><i></i><i class="on"></i><i></i></div>
</section>

<h2 class="abs intro__title">The <span class="accent">PRAGUE</span> rental expert for your vacation</h2>
<p class="abs intro__sub">Prague offers diverse villas in different regions to help you spend your dream vacation. Book your villa online quickly and safely.</p>

<div class="abs field__label" style="left:128px">Check In</div>
<div class="abs field__label" style="left:402px">Check Out</div>
<div class="abs field__label" style="left:668px">Adults</div>
<div class="abs field__label" style="left:795px">Children</div>
<div class="abs field" style="left:126px;width:249px">00/00/2018 <svg width="16" height="16" viewBox="0 0 16 16"><rect x="1" y="3" width="14" height="12" fill="none" stroke="#cf9f3b" stroke-width="1.5"/><path d="M1 7h14M5 1v4M11 1v4" stroke="#cf9f3b" stroke-width="1.5"/></svg></div>
<div class="abs field" style="left:397px;width:250px">00/00/2018 <svg width="16" height="16" viewBox="0 0 16 16"><rect x="1" y="3" width="14" height="12" fill="none" stroke="#cf9f3b" stroke-width="1.5"/><path d="M1 7h14M5 1v4M11 1v4" stroke="#cf9f3b" stroke-width="1.5"/></svg></div>
<div class="abs field" style="left:668px;width:105px">0 <svg width="10" height="6" viewBox="0 0 10 6"><path d="M1 1l4 4 4-4" fill="none" stroke="#888" stroke-width="1.5"/></svg></div>
<div class="abs field" style="left:795px;width:101px">0 <svg width="10" height="6" viewBox="0 0 10 6"><path d="M1 1l4 4 4-4" fill="none" stroke="#888" stroke-width="1.5"/></svg></div>
<div class="search btn">SEARCH</div>

<div class="abs promo" style="left:77px">
  <div class="photo promo__img" style="background:linear-gradient(135deg,#8c6a52,#d9d2c6)" role="img" aria-label="Living room with brick wall"></div>
  <div class="promo__cap promo__cap--gold">BRAND NEW Luxury Living<br>Stunning Contemporary Design</div>
</div>
<div class="abs promo" style="left:427px">
  <div class="photo promo__img" style="background:linear-gradient(135deg,#6e5236,#e2d8c8)" role="img" aria-label="Attic apartment with wooden beams"></div>
  <div class="promo__cap promo__cap--dark">BRAND NEW ZEN Luxury Living<br>Apartment in the Center of Prague</div>
</div>
<div class="abs promo" style="left:778px">
  <div class="photo promo__img" style="background:linear-gradient(135deg,#b9b1a4,#f0ece6)" role="img" aria-label="Bright loft living room"></div>
  <div class="promo__cap promo__cap--dark">EXPEDITION PRAGUE! TOP LOCAL<br>BRAND NEW APARTMENT</div>
</div>

<section class="services">
  <div class="photo services__bg" role="img" aria-label="Dim apartment interior background"></div>
  <h2 class="abs services__title"><span class="accent">PRAGUE</span> Services</h2>
  <p class="abs services__text">Vltava Suites offers short term and as well as long term options in our studio apartments and our one bedroom apartment homes.our luxurious apartments and high quality customer services have allowed us to dominate the prague apartment market with a proven track record. Our years of experience and knowledge have made us a premier apartment rental company as we continue to stress the importance of servicing individuals and corporations who are the seeking the finest accomodations.</p>

  <div class="abs svc" style="left:77px">
    <div class="svc__box"></div>
    <div class="photo svc__img" role="img" aria-label="Sunny penthouse bedroom"></div>
    <div class="svc__badge" style="left:168px;top:-4px">1</div>
    <div class="svc__badge" style="left:192px;top:140px">4</div>
    <div class="svc__cap">BRAND NEW SUNNY PENTHOUSE WITH A VIEW OF PRAGUE</div>
    <div class="svc__btn btn">DETAILS</div>
  </div>
  <div class="abs svc" style="left:343px">
    <div class="svc__box"></div>
    <div class="photo svc__img" style="background:#8d8276" role="img" aria-label="Apartment living area"></div>
    <div class="svc__badge" style="left:168px;top:-4px">1</div>
    <div class="svc__badge" style="left:192px;top:140px">2</div>
    <div class="svc__cap">BRAND NEW APARTMENT UNBEATABLE LOCATION</div>
    <div class="svc__btn btn">DETAILS</div>
  </div>
  <div class="abs svc" style="left:609px">
    <div class="svc__box"></div>
    <div class="photo svc__img" style="background:#b3a794" role="img" aria-label="Penthouse lounge"></div>
    <div class="svc__badge" style="left:168px;top:-4px">1</div>
    <div class="svc__badge" style="left:192px;top:140px">4</div>
    <div class="svc__cap">BRAND NEW SUNNY PENTHOUSE WITH A VIEW OF PRAGUE</div>
    <div class="svc__btn btn">DETAILS</div>
  </div>
  <div class="abs svc" style="left:876px">
    <div class="svc__box"></div>
    <div class="photo svc__img" style="background:#c9c1b5" role="img" aria-label="Attic bedroom"></div>
    <div class="svc__badge" style="left:168px;top:-4px">1</div>
    <div class="svc__badge" style="left:192px;top:140px">4</div>
    <div class="svc__cap">BRAND NEW APARTMENT UNBEATABLE LOCATION</div>
    <div class="svc__btn btn">DETAILS</div>
  </div>
</section>

<div class="photo thumb" style="top:2233px;height:96px" role="img" aria-label="Apartment room thumbnail"></div>
<div class="photo thumb" style="top:2348px;height:99px;background:#aaa49b" role="img" aria-label="Apartment room thumbnail"></div>
<div class="photo thumb" style="top:2463px;height:102px;background:#b7b1a8" role="img" aria-label="Apartment room thumbnail"></div>
<div class="photo offer__main" role="img" aria-label="Bright attic bedroom with skylights"></div>
<div class="offer__bar"><span>Start Form : 150$ USD</span><span>CHECK AVIABILITY</span></div>
<h2 class="abs offer__title"><span class="accent">PRAGUE</span> Exclusive<br>Offer &amp; Tours</h2>
<p class="abs offer__text">Lorem Ipsum is simply dummy text of the printing and typesetting industry. Lorem Ipsum has been the industry's standard dummy text ever since the 1500s, when an unknown printer took a galley of type and scrambled it to make a type specimen book. It has survived not only five centuries.</p>
<div class="offer__btn btn">READ MORE</div>

<section class="voices">
  <div class="photo voices__bg" role="img" aria-label="Gold-tinted collage of guest portraits"></div>
  <h2 class="abs voices__title">What Our Visiter Say</h2>
  <div class="photo voices__avatar" role="img" aria-label="Guest portrait"></div>
  <p class="abs voices__quote">" Lorem Ipsum is simply dummy text of the printing and typesetting industry. Lorem Ipsum has been the industry's standard dummy text ever since the 1500s."</p>
  <div class="abs voices__name">MIRA NOVAK</div>
  <div class="abs voices__role">Manager, PRAGUE Apartment</div>
  <div class="abs voices__dots"><i></i><i class="on"></i><i></i></div>
</section>

<h2 class="abs blog__title"><span class="accent">Recent</span> Blog</h2>
<article class="abs post" style="left:77px">
  <div class="photo post__img" style="background:linear-gradient(135deg,#5c4a3e,#c5b8a8)" role="img" aria-label="Family arriving at apartment"></div>
  <div class="post__date"><b>20</b><span>Nov</span></div>
  <h3 class="post__title">Lorem Ipsum text printing typesetting industry.</h3>
  <p class="post__text">Lorem Ipsum is simply dummy text of the printing and typesetting industry. Lorem Ipsum has been the industry's standard dummy text ever since the 1500s, when an unknown printer.</p>
</article>
<article class="abs post" style="left:433px">
  <div class="photo post__img" style="background:linear-gradient(135deg,#a89880,#e6ddd0)" role="img" aria-label="Couple relaxing at home"></div>
  <div class="post__date"><b>20</b><span>Nov</span></div>
  <h3 class="post__title">Lorem Ipsum text printing typesetting industry.</h3>
  <p class="post__text">Lorem Ipsum is simply dummy text of the printing and typesetting industry. Lorem Ipsum has been the industry's standard dummy text ever since the 1500s, when an unknown printer.</p>
</article>
<article class="abs post" style="left:789px">
  <div class="photo post__img" style="background:linear-gradient(135deg,#7fa6c8,#b8633a)" role="img" aria-label="Modern apartment building facade"></div>
  <div class="post__date"><b>20</b><span>Nov</span></div>
  <h3 class="post__title">Lorem Ipsum text printing typesetting industry.</h3>
  <p class="post__text">Lorem Ipsum is simply dummy text of the printing and typesetting industry. Lorem Ipsum has been the industry's standard dummy text ever since the 1500s, when an unknown printer.</p>
</article>

<footer class="footer">
  <h4 style="left:77px">About Us</h4>
  <p class="footer__about">Lorem Ipsum is simply dummy text of the printing and typesetting industry. Lorem Ipsum is simply dummy text of the printing and typesetting industry. Lorem Ipsum is simply dummy text of the printing and typesetting industry.</p>
  <h4 style="left:384px">Site Map</h4>
  <ul class="footer__map">
    <li>Home</li><li>Apartments</li><li>Location</li><li>Services</li><li>Gallery</li><li>News</li><li>Exclusive Offers and Tour</li><li>Contact Us</li>
  </ul>
  <h4 style="left:586px">Contact Us</h4>
  <div class="footer__contact">
    <div class="footer__row"><svg width="16" height="20" viewBox="0 0 16 20"><path d="M8 0a7 7 0 0 1 7 7c0 5-7 13-7 13S1 12 1 7a7 7 0 0 1 7-7z" fill="#cf9f3b"/><circle cx="8" cy="7" r="2.5" fill="#222"/></svg><div><b>VLTAVA SUITES</b><br>United States</div></div>
    <div class="footer__row"><svg width="18" height="18" viewBox="0 0 24 24"><path d="M6 2l4 4-2 3c1 3 4 6 7 7l3-2 4 4-3 4C10 21 3 14 2 5z" fill="#cf9f3b"/></svg><div>+420 555 010 200</div></div>
    <div class="footer__row"><svg width="18" height="14" viewBox="0 0 18 14"><rect width="18" height="14" fill="#cf9f3b"/><path d="M0 0l9 8 9-8" fill="none" stroke="#222" stroke-width="1.5"/></svg><div>stay@vltavasuites.com</div></div>
  </div>
  <h4 style="left:877px">Newsletter</h4>
  <div class="footer__news">
    Would you like to receive exclusive access to articles, white papers and our regular monthly newsletter?
    <div class="footer__input">Enter Email Id</div>
    <div class="footer__btn btn">SUBSCRIBE</div>
  </div>
</footer>
<div class="copy">copyright | VLTAVASUITES - 2017 All Right Reserved</div>

</body>
</html>
```